I need a fresh looking, exciting and loaded design for Full service Restaurant

We need a web design for our restaurant, which offers full service Pakistani and Indian food in PA, USA. Design should be elegant, simplified so customers can navigate easily and order food online for catering as well as delivery. We need loads of pictures and room to grow. I already have a web address via vemrilo.com. It should include SSL and e-commerce for ordering food.
Be original and be creative and make it a fun site :)

```html
<!DOCTYPE html>
<html lang="en">
<head>
<meta charset="utf-8">
<title>Saffron Lane – Fine Pak-Indian Cuisine</title>
<link rel="stylesheet" href="https://fonts.googleapis.com/css2?family=Open+Sans:wght@400;600;700&family=Yellowtail&display=swap">
<style>
:root{
  --red:#d71c1c;
  --green:#3f7a1a;
  --dark-green:#2f5f12;
  --ink:#333333;
  --muted:#8a8a8a;
  --line:#e3e3e3;
  --white:#ffffff;
  --btn:#2b2b2b;
}
*{box-sizing:border-box;margin:0;padding:0}
html,body{width:1200px;height:2903px;overflow:hidden}
body{position:relative;font-family:"Open Sans",Arial,sans-serif;color:var(--ink);background:var(--white)}
.abs{position:absolute}
.script{font-family:"Yellowtail",cursive;font-weight:400;white-space:nowrap}

/* hero */
.hero{left:0;top:0;width:1200px;height:660px;background:linear-gradient(120deg,#eae6e0 0%,#f3ece4 35%,#d9e2c4 60%,#e7d7c8 85%,#f0ece6 100%)}
.social-top{left:80px;top:64px;display:flex;gap:18px}
.social-top span{width:34px;height:34px;border-radius:50%;background:var(--dark-green);display:block}
.brand{left:0;width:1200px;top:50px;text-align:center}
.brand-name{font-weight:700;font-size:40px;color:var(--green);line-height:1}
.brand-tag{font-size:13px;color:var(--dark-green);margin-top:6px}
.contact-top{left:958px;top:50px;font-size:15px;color:var(--ink);white-space:nowrap}
.contact-top div{display:flex;align-items:center;gap:12px;height:32px}
.contact-top .phone{font-size:20px}
.nav{left:79px;top:153px;width:1039px;height:43px;background:var(--red);border-radius:4px;display:flex;justify-content:space-between;align-items:center;padding:0 50px 0 48px}
.nav a{font-family:"Yellowtail",cursive;color:var(--white);text-decoration:none;font-size:20px;white-space:nowrap}
.hero-title{left:0;top:345px;width:1200px;text-align:center;font-size:74px;color:var(--red)}
.hero-title em{font-style:normal;color:var(--dark-green)}
.dots{left:537px;top:622px;display:flex;gap:18px}
.dots span{width:12px;height:12px;border:2px solid var(--dark-green);border-radius:50%}
.dots .on{background:var(--red);border-color:var(--red)}

/* welcome */
.welcome-pre{left:0;width:680px;top:768px;text-align:center;font-size:32px;color:var(--green)}
.welcome-name{left:0;width:680px;top:800px;text-align:center;font-size:62px;color:var(--red)}
.welcome-text{left:110px;width:460px;top:914px;text-align:center;font-size:12.5px;line-height:23px;color:var(--muted)}
.read-more{left:0;width:680px;top:1002px;text-align:center;font-size:28px;color:var(--green)}
.welcome-photo{left:623px;top:722px;width:495px;height:352px;background:linear-gradient(135deg,#3f5a2a,#c48a55 45%,#e8d9c0 70%,#6b8b3c)}
.badge{left:888px;top:846px;width:230px;height:118px;background:var(--red);color:var(--white);text-align:center;padding-top:36px}
.badge b{font-size:26px;display:block;line-height:1}
.badge small{font-size:11px}

/* specials */
.specials-bg{left:0;top:1157px;width:1200px;height:619px;background:linear-gradient(100deg,#e8ecef,#f4efe7 50%,#f2e3b9 75%,#e8ecef)}
.specials-card{left:79px;top:1248px;width:1039px;height:434px;background:var(--white);box-shadow:0 2px 14px rgba(0,0,0,.12)}
.specials-photo{left:79px;top:1248px;width:351px;height:434px;background:linear-gradient(150deg,#6b4b2c,#d9b23a 40%,#f0eee6 55%,#3b2d2a 75%,#8a3a2a)}
.grill{left:79px;top:1560px;width:250px;height:122px;background:var(--red);color:var(--white);text-align:center;padding-top:30px}
.grill .script{font-size:32px;display:block;line-height:1}
.grill .script em{font-style:normal;color:#9acd4a}
.grill small{font-size:14px}
.specials-title{left:430px;width:688px;top:1278px;text-align:center;font-size:56px;color:var(--red);line-height:1.1}
.specials-sub{left:430px;width:688px;top:1337px;text-align:center;font-size:14px;color:var(--green)}
.special{width:280px;text-align:center}
.special .name{font-family:"Yellowtail",cursive;font-size:26px;color:#222;line-height:1;white-space:nowrap}
.special .price{font-size:19px;color:var(--green)}
.divider{height:1px;background:var(--line);width:280px}
.divider i{position:absolute;left:137px;top:-3px;width:6px;height:6px;border-radius:50%;background:var(--green)}

/* menu */
.menu-title{left:0;width:1200px;top:1812px;text-align:center;font-size:62px;color:var(--red)}
.menu-head{top:1923px;width:497px;height:45px;background:var(--green);border-radius:3px;color:var(--white);text-align:center;font-size:22px;line-height:45px}
.dish{width:477px;height:100px}
.dish .thumb{position:absolute;left:0;top:0;width:76px;height:76px;border-radius:50%;border:4px solid #f1f1f1;box-shadow:0 1px 4px rgba(0,0,0,.15)}
.dish .row{position:absolute;left:101px;right:0;top:4px;display:flex;justify-content:space-between;font-size:13px;padding-bottom:8px;border-bottom:1px solid var(--line)}
.dish .row b{font-weight:600;color:#222}
.dish .row span{color:var(--green);font-weight:600}
.dish p{position:absolute;left:101px;right:0;top:36px;font-size:12.5px;line-height:23px;color:var(--muted)}

/* newsletter */
.newsletter{left:0;top:2423px;width:1200px;height:93px;background:var(--red)}
.nl-label{left:214px;top:2456px;width:184px;text-align:right;font-size:18px;line-height:30px;color:var(--white)}
.nl-input{left:414px;top:2451px;width:379px;height:38px;background:var(--white);border-radius:3px;font-size:12px;color:var(--muted);padding:11px 16px}
.nl-btn{left:803px;top:2451px;width:132px;height:38px;background:var(--btn);border-radius:3px;color:var(--white);font-size:20px;text-align:center;line-height:38px}

/* footer */
.footer{left:0;top:2516px;width:1200px;height:387px;background:linear-gradient(120deg,#2f5a12,#3c6e1a 40%,#2f5a12 70%,#41741d)}
.foot-brand{left:0;width:1200px;top:2600px;text-align:center;color:var(--white)}
.foot-brand b{font-size:32px;display:block;line-height:1}
.foot-brand small{font-size:11px}
.foot-social{left:494px;top:2694px;display:flex;gap:30px}
.foot-social span{width:18px;height:18px;border-radius:50%;background:var(--white)}
.foot-contacts{left:0;top:2766px;width:1200px;display:flex;justify-content:center;color:var(--white);font-size:16px;white-space:nowrap}
.foot-contacts div{display:flex;align-items:center;gap:12px;padding:0 44px;height:34px}
.foot-contacts div+div{border-left:1px solid rgba(255,255,255,.3)}
.copy{left:0;width:1200px;top:2833px;text-align:center;color:var(--white);font-size:13px}
</style>
</head>
<body>

<section class="abs hero" role="img" aria-label="Close-up photo of grilled chicken with fresh green salad"></section>
<div class="abs social-top"><span></span><span></span><span></span></div>
<div class="abs brand"><div class="brand-name">Saffron Lane</div><div class="brand-tag">A fine Pak-Indian Cuisine</div></div>
<div class="abs contact-top">
  <div class="phone"><svg width="14" height="22" viewBox="0 0 14 22"><rect x="1" y="1" width="12" height="20" rx="2" fill="none" stroke="#222" stroke-width="2"/><circle cx="7" cy="17" r="1.4" fill="#222"/></svg>555-014-2780</div>
  <div><svg width="18" height="13" viewBox="0 0 18 13"><rect width="18" height="13" rx="1" fill="#222"/><path d="M1 1l8 6 8-6" stroke="#fff" fill="none" stroke-width="1.5"/></svg>info@saffronlane.com</div>
</div>
<nav class="abs nav"><a>Home</a><a>About us</a><a>Menu</a><a>Recipes</a><a>Reservation</a><a>Contact us</a></nav>
<h1 class="abs hero-title script">Delicious <em>Food</em></h1>
<div class="abs dots"><span></span><span></span><span class="on"></span><span></span><span></span></div>

<h2 class="abs welcome-pre script">Welcome to</h2>
<h2 class="abs welcome-name script">Saffron Lane</h2>
<p class="abs welcome-text">Lorem ipsum dolor sit amet, consectetur adipiscing elit. Quisque consequat, ex ac commodo gravida, massa ex fringilla augue, eu gravida arcu elit ut est. Aliquam ipsum dolor, sodales sed nulla auctor, molestie hendrerit elit.</p>
<div class="abs read-more script">Read More</div>
<div class="abs welcome-photo" role="img" aria-label="Photo of stuffed avocado halves with herbs"></div>
<div class="abs badge"><b>Saffron Lane</b><small>A fine Pak-Indian Cuisine</small></div>

<section class="abs specials-bg" role="img" aria-label="Soft-focus photo of a seafood plate with lemon"></section>
<div class="abs specials-card"></div>
<div class="abs specials-photo" role="img" aria-label="Photo of rice, beans and sausage on a yellow plate"></div>
<div class="abs grill"><span class="script">Summer <em>Grill</em></span><small>Starts from 19.99$</small></div>
<h2 class="abs specials-title script">Specials</h2>
<div class="abs specials-sub">Check out Our Offers</div>

<div class="abs special" style="left:479px;top:1402px"><div class="name">Indian Strip Steak</div><div class="price">$28.99</div></div>
<div class="abs special" style="left:789px;top:1402px"><div class="name">Black Angus Steak</div><div class="price">$95.99</div></div>
<div class="abs divider" style="left:479px;top:1474px"><i></i></div>
<div class="abs divider" style="left:789px;top:1474px"><i></i></div>
<div class="abs special" style="left:479px;top:1495px"><div class="name">Porthouse Steak</div><div class="price">$17.99</div></div>
<div class="abs special" style="left:789px;top:1495px"><div class="name">Rib eye Steak</div><div class="price">$28.99</div></div>
<div class="abs divider" style="left:479px;top:1567px"><i></i></div>
<div class="abs divider" style="left:789px;top:1567px"><i></i></div>
<div class="abs special" style="left:479px;top:1588px"><div class="name">Sailsbury Steak</div><div class="price">$23.00</div></div>
<div class="abs special" style="left:789px;top:1588px"><div class="name">Wellington Steak</div><div class="price">$67.99</div></div>

<h2 class="abs menu-title script">Menu</h2>
<div class="abs menu-head script" style="left:79px">Breakfast &amp; Dinner</div>
<div class="abs menu-head script" style="left:621px">Lunch Foods</div>

<div class="abs dish" style="left:82px;top:2025px"><div class="thumb" role="img" aria-label="Salad dish photo" style="background:#b9c77a"></div><div class="row"><b>Indian Strip Steak</b><span>$28.99</span></div><p>Lorem ipsum dolor sit amet, consectetur adipiscing elit. Quisque ipsum dolor sit amet.</p></div>
<div class="abs dish" style="left:82px;top:2146px"><div class="thumb" role="img" aria-label="Dumplings dish photo" style="background:#c9a77a"></div><div class="row"><b>Black Angus Steak</b><span>$49.99</span></div><p>Lorem ipsum dolor sit amet, consectetur adipiscing elit. Quisque ipsum dolor sit amet.</p></div>
<div class="abs dish" style="left:82px;top:2267px"><div class="thumb" role="img" aria-label="Chocolate dessert photo" style="background:#6b4a3a"></div><div class="row"><b>Wellington Steak</b><span>$67.99</span></div><p>Lorem ipsum dolor sit amet, consectetur adipiscing elit. Quisque ipsum dolor sit amet.</p></div>

<div class="abs dish" style="left:630px;top:2025px"><div class="thumb" role="img" aria-label="Dumplings dish photo" style="background:#c9a77a"></div><div class="row"><b>Indian Strip Steak</b><span>$28.99</span></div><p>Lorem ipsum dolor sit amet, consectetur adipiscing elit. Quisque ipsum dolor sit amet.</p></div>
<div class="abs dish" style="left:630px;top:2146px"><div class="thumb" role="img" aria-label="Salad dish photo" style="background:#b9c77a"></div><div class="row"><b>Black Angus Steak</b><span>$49.99</span></div><p>Lorem ipsum dolor sit amet, consectetur adipiscing elit. Quisque ipsum dolor sit amet.</p></div>
<div class="abs dish" style="left:630px;top:2267px"><div class="thumb" role="img" aria-label="Chocolate dessert photo" style="background:#6b4a3a"></div><div class="row"><b>Wellington Steak</b><span>$67.99</span></div><p>Lorem ipsum dolor sit amet, consectetur adipiscing elit. Quisque ipsum dolor sit amet.</p></div>

<section class="abs newsletter"></section>
<div class="abs nl-label script">Get Our Newsletter</div>
<div class="abs nl-input">Enter Your email Address
  <svg style="position:absolute;right:10px;top:11px" width="20" height="15" viewBox="0 0 20 15"><rect x="1" y="1" width="18" height="13" fill="none" stroke="#777" stroke-width="1.4"/><path d="M1 1l9 7 9-7" fill="none" stroke="#777" stroke-width="1.4"/></svg>
</div>
<div class="abs nl-btn script">Subscribe</div>

<footer class="abs footer" role="img" aria-label="Dark green tinted food photo background"></footer>
<div class="abs foot-brand"><b>Saffron Lane</b><small>A fine Pak-Indian Cuisine</small></div>
<div class="abs foot-social"><span></span><span></span><span></span><span></span><span></span></div>
<div class="abs foot-contacts">
  <div><svg width="12" height="20" viewBox="0 0 12 20"><rect x="1" y="1" width="10" height="18" rx="2" fill="none" stroke="#fff" stroke-width="2"/><circle cx="6" cy="15.5" r="1.3" fill="#fff"/></svg>800-555-0142</div>
  <div><svg width="18" height="13" viewBox="0 0 18 13"><rect width="18" height="13" rx="1" fill="#fff"/><path d="M1 1l8 6 8-6" stroke="#3c6e1a" fill="none" stroke-width="1.5"/></svg>info@saffronlane.com</div>
  <div><svg width="14" height="20" viewBox="0 0 14 20"><path d="M7 0a7 7 0 0 1 7 7c0 5-7 13-7 13S0 12 0 7a7 7 0 0 1 7-7z" fill="#fff"/><circle cx="7" cy="7" r="2.6" fill="#3c6e1a"/></svg>118, Linden Row, North Harbor VIC 3050</div>
</div>
<div class="abs copy">© 2016. Saffron Lane | All Rights Reserved.</div>

</body>
</html>
```